Redesign of business card for Cedar Ridge Mechanical

We are looking for a new design for our business cards for Cedar Ridge Mechanical. We are a plumbing & HVAC construction company, operating on the West Coast of Canada and USA. Logo attached.
Industry/Entity Type
Construction - Plumbing & HVAC
Contact Information for Business Card
Name, address, phone numbers, email, website address
Look and feel
Each slider illustrates characteristics of the customer's brand and the style your logo design should communicate.

```html
<!DOCTYPE html>
<html lang="en">
<head>
<meta charset="utf-8">
<title>Cedar Ridge Mechanical – Business Cards</title>
<link href="https://fonts.googleapis.com/css2?family=Poppins:wght@300;400;500;600;700&display=swap" rel="stylesheet">
<style>
  :root {
    --backdrop: #1f1f21;
    --card-ink: #232325;
    --rim: #ffffff;
    --text: #ffffff;
    --text-soft: #e6e6e6;
  }
  html, body {
    margin: 0;
    padding: 0;
    width: 1200px;
    height: 711px;
    overflow: hidden;
    background: var(--backdrop);
    font-family: "Poppins", sans-serif;
    color: var(--text);
  }
  .canvas {
    position: relative;
    width: 1200px;
    height: 711px;
  }
  .card {
    position: absolute;
    top: 196px;
    width: 540px;
    height: 318px;
  }
  .card--front { left: 45px; }
  .card--back { left: 615px; }
  .card__frame {
    position: absolute;
    inset: 0;
    width: 540px;
    height: 318px;
  }
  .brand {
    position: absolute;
    display: flex;
    align-items: center;
    gap: 12px;
    font-weight: 600;
    text-transform: uppercase;
    letter-spacing: 1.5px;
  }
  .brand__mark {
    flex: none;
    border: 4px solid var(--rim);
    box-sizing: border-box;
  }
  .card--front .brand {
    left: 50%;
    top: 50%;
    transform: translate(-50%, -50%);
    font-size: 22px;
    white-space: nowrap;
  }
  .card--front .brand__mark { width: 34px; height: 34px; }
  .card--back .brand {
    left: 42px;
    top: 138px;
    gap: 10px;
    font-size: 16px;
    line-height: 1.25;
  }
  .card--back .brand__mark { width: 30px; height: 30px; border-width: 3px; }
  .card--back .brand__name { width: 150px; }
  .divider {
    position: absolute;
    left: 252px;
    top: 60px;
    width: 1px;
    height: 150px;
    background: var(--rim);
    opacity: 0.85;
  }
  .person {
    position: absolute;
    left: 282px;
    top: 66px;
  }
  .person__name {
    margin: 0;
    font-size: 24px;
    line-height: 1.1;
    font-weight: 300;
  }
  .person__name strong { font-weight: 700; }
  .person__title {
    margin: 2px 0 0;
    font-size: 12px;
    font-weight: 400;
    color: var(--text-soft);
  }
  .contacts {
    position: absolute;
    left: 290px;
    top: 140px;
    margin: 0;
    padding: 0;
    list-style: none;
    font-size: 12.5px;
    font-weight: 300;
    white-space: nowrap;
  }
  .contacts li {
    display: flex;
    align-items: center;
    gap: 9px;
    height: 20px;
  }
  .contacts svg { width: 12px; height: 12px; flex: none; }
  .address {
    position: absolute;
    left: 0;
    right: 0;
    bottom: 38px;
    margin: 0;
    text-align: center;
    font-size: 12.5px;
    font-weight: 300;
  }
</style>
</head>
<body>
<main class="canvas">

  <section class="card card--front" aria-label="Business card front">
    <svg class="card__frame" viewBox="0 0 540 318" aria-hidden="true">
      <rect x="0" y="0" width="540" height="318" rx="24" fill="var(--rim)"/>
      <rect x="13" y="13" width="514" height="292" rx="12" fill="var(--card-ink)"/>
      <rect x="58" y="0" width="6" height="14" fill="var(--card-ink)"/>
      <rect x="476" y="0" width="6" height="14" fill="var(--card-ink)"/>
      <rect x="58" y="304" width="6" height="14" fill="var(--card-ink)"/>
      <rect x="476" y="304" width="6" height="14" fill="var(--card-ink)"/>
    </svg>
    <div class="brand">
      <span class="brand__mark"></span>
      <span class="brand__name">Cedar Ridge Mechanical</span>
    </div>
  </section>

  <section class="card card--back" aria-label="Business card back">
    <svg class="card__frame" viewBox="0 0 540 318" aria-hidden="true">
      <rect x="0" y="0" width="540" height="318" rx="24" fill="var(--rim)"/>
      <rect x="13" y="13" width="514" height="292" rx="12" fill="var(--card-ink)"/>
      <rect x="58" y="0" width="6" height="14" fill="var(--card-ink)"/>
      <rect x="476" y="0" width="6" height="14" fill="var(--card-ink)"/>
      <rect x="58" y="304" width="6" height="14" fill="var(--card-ink)"/>
      <rect x="476" y="304" width="6" height="14" fill="var(--card-ink)"/>
    </svg>

    <div class="brand">
      <span class="brand__mark"></span>
      <span class="brand__name">Cedar Ridge Mechanical</span>
    </div>

    <div class="divider"></div>

    <div class="person">
      <h1 class="person__name"><strong>Marta</strong> Kovar</h1>
      <p class="person__title">Founder &amp; CEO</p>
    </div>

    <ul class="contacts">
      <li>
        <svg viewBox="0 0 24 24" aria-hidden="true"><path fill="#fff" d="M6.6 10.8a15 15 0 0 0 6.6 6.6l2.2-2.2c.3-.3.7-.4 1-.2 1.1.4 2.3.6 3.6.6.6 0 1 .4 1 1V20c0 .6-.4 1-1 1C10.6 21 3 13.4 3 4c0-.6.4-1 1-1h3.5c.6 0 1 .4 1 1 0 1.3.2 2.5.6 3.6.1.3 0 .7-.2 1z"/></svg>
        <span>(555) 214-0387</span>
      </li>
      <li>
        <svg viewBox="0 0 24 24" aria-hidden="true"><circle cx="12" cy="12" r="9" fill="none" stroke="#fff" stroke-width="2.2"/><path d="M3 12h18M12 3c3 3 3 15 0 18M12 3c-3 3-3 15 0 18" fill="none" stroke="#fff" stroke-width="1.8"/></svg>
        <span>info@cedarridgemech.com</span>
      </li>
      <li>
        <svg viewBox="0 0 24 24" aria-hidden="true"><rect x="2" y="5" width="20" height="14" rx="1.5" fill="none" stroke="#fff" stroke-width="2"/><path d="M2.5 6 12 13l9.5-7" fill="none" stroke="#fff" stroke-width="2"/></svg>
        <span>www.cedarridgemech.com</span>
      </li>
    </ul>

    <p class="address">418 Harbor Ln. Suite 120 Bellingham, WA 98225</p>
  </section>

</main>
</body>
</html>
```